Structural Engineering Business Card

Brookvane Drafting does residential house plans for clients in Central Florida. Would like simple but elegant business card that is appropriate for a house plan engineering company. Prefer black business card with black/white them but open to other shades of blue. I uploaded a sample card that I came across that looked good but please come up with your own creative designs.

Contact Information for Business Card

Name, Title, Phone, Email, Address, website

```html
<!DOCTYPE html>
<html lang="en">
<head>
<meta charset="utf-8">
<title>Brookvane Drafting — Business Card</title>
<link href="https://fonts.googleapis.com/css2?family=Poppins:wght@400;700;800&display=swap" rel="stylesheet">
<style>
  :root {
    --stage: #2b2b2d;
    --card-white: #ffffff;
    --card-black: #1a1b1d;
    --ink: #0d0d0d;
    --rule: #9a9a9a;
    --pattern-a: #26272a;
    --pattern-b: #1c1d1f;
    --paper-text: #ffffff;
  }
  * { box-sizing: border-box; margin: 0; padding: 0; }
  html, body {
    width: 1200px; height: 1108px; overflow: hidden;
    background: var(--stage);
    font-family: "Poppins", sans-serif;
  }
  .stage {
    position: relative; width: 1200px; height: 1108px;
    display: flex; justify-content: center; align-items: center; gap: 70px;
  }
  .card {
    width: 440px; height: 740px; border-radius: 26px;
    position: relative; overflow: hidden;
  }
  /* Front */
  .card--front {
    background: var(--card-white); color: var(--ink);
    display: flex; flex-direction: column; align-items: center;
    padding: 110px 36px 60px;
  }
  .brand {
    font-weight: 800; font-size: 40px; line-height: 1.05;
    text-align: center; letter-spacing: 0.5px; text-transform: uppercase;
    display: flex; align-items: center; gap: 14px;
  }
  .brand__mark { width: 22px; height: 22px; background: var(--ink); flex: none; }
  .contact { margin-top: auto; text-align: center; width: 100%; }
  .contact__name { font-weight: 700; font-size: 30px; letter-spacing: 0.5px; text-transform: uppercase; }
  .contact__title { font-size: 20px; margin-top: 2px; }
  .icon-row {
    display: flex; align-items: center; gap: 8px; margin: 14px 0 12px;
  }
  .icon-row::before, .icon-row::after {
    content: ""; flex: 1; height: 1px; background: var(--rule);
  }
  .icon {
    width: 34px; height: 34px; background: var(--ink); border-radius: 5px;
    display: flex; align-items: center; justify-content: center;
  }
  .icon svg { width: 20px; height: 20px; }
  .contact__line { font-size: 20px; line-height: 1.4; }
  .divider { height: 1px; background: var(--rule); margin: 16px 20px; }
  /* Back */
  .card--back { background: var(--card-black); }
  .pattern {
    position: absolute; inset: 0;
    background: linear-gradient(135deg, var(--pattern-a) 0%, var(--pattern-b) 60%, var(--pattern-a) 100%);
  }
  .back-brand {
    position: absolute; left: 0; right: 0; top: 50%; transform: translateY(-50%);
    display: flex; justify-content: center; align-items: center; gap: 10px;
    color: var(--paper-text); font-weight: 800; font-size: 22px;
    letter-spacing: 0.5px; text-transform: uppercase;
  }
  .back-brand__mark { width: 12px; height: 12px; background: var(--paper-text); }
</style>
</head>
<body>
<main class="stage">
  <section class="card card--front" aria-label="Card front">
    <div class="brand"><span class="brand__mark"></span><span>Brookvane<br>Drafting</span></div>
    <div class="contact">
      <p class="contact__name">Marcus Hale</p>
      <p class="contact__title">Managing Director</p>
      <div class="icon-row">
        <span class="icon" aria-label="Phone">
          <svg viewBox="0 0 24 24" fill="#fff"><path d="M6.6 10.8a15 15 0 0 0 6.6 6.6l2.2-2.2a1 1 0 0 1 1-.25 11.4 11.4 0 0 0 3.6.57 1 1 0 0 1 1 1V20a1 1 0 0 1-1 1A17 17 0 0 1 3 4a1 1 0 0 1 1-1h3.5a1 1 0 0 1 1 1c0 1.25.2 2.45.57 3.57a1 1 0 0 1-.25 1z"/></svg>
        </span>
        <span class="icon" aria-label="Email">
          <svg viewBox="0 0 24 24" fill="none" stroke="#fff" stroke-width="2"><rect x="3" y="5" width="18" height="14" rx="1"/><path d="M3 6l9 7 9-7"/></svg>
        </span>
        <span class="icon" aria-label="Website">
          <svg viewBox="0 0 24 24" fill="none" stroke="#fff" stroke-width="2"><circle cx="12" cy="12" r="9"/><path d="M3 12h18M12 3c3 3 3 15 0 18M12 3c-3 3-3 15 0 18"/></svg>
        </span>
      </div>
      <p class="contact__line">407-555 0142</p>
      <p class="contact__line">info@brookvanedrafting.com</p>
      <p class="contact__line">www.brookvanedrafting.com</p>
      <div class="divider"></div>
      <p class="contact__line">421, Address line goes here</p>
      <p class="contact__line">45452,Country Name</p>
    </div>
  </section>

  <section class="card card--back" aria-label="Card back">
    <div class="pattern" role="img" aria-label="Tonal repeating brand-name pattern in glossy black on matte black"></div>
    <div class="back-brand"><span class="back-brand__mark"></span><span>Brookvane Drafting</span></div>
  </section>
</main>
</body>
</html>
```